Veltrano.co - Polar Expeditions Specialists

We need a modern, visually striking business card for Veltrano.co, a company specialized in selling expedition cruises to the most remote regions on Earth, with a focus on the Arctic and Antarctica. The design should instantly communicate that the cardholder is an expert in polar travel. Use clean, premium aesthetics with cool tones like icy blue and white, possibly incorporating polar imagery (ice, glaciers, penguins, etc.)

Attached the logo

Contact Information for Business Card

Feels high-end and trustworthy.. Visually memorable — encourages people to keep it

Colors
0054AA
0677BA
7BADD7
CADEEF
E8F1F8

Requirements
Must have
• ice, glaciers, penguins, montains
Nice to have
• modern, transparente,

```html
<!DOCTYPE html>
<html lang="en">
<head>
<meta charset="utf-8">
<title>Veltrano.co Business Card</title>
<link href="https://fonts.googleapis.com/css2?family=Poppins:wght@400;500;600;700&display=swap" rel="stylesheet">
<style>
  :root {
    --brand-blue: #2f6fb0;
    --deep-blue: #0054aa;
    --ice-white: #ffffff;
    --frost: #e8f1f8;
    --ink: #1c1c1c;
    --backdrop: #eef2f6;
  }
  * { margin: 0; padding: 0; box-sizing: border-box; }
  html, body {
    width: 1200px; height: 900px; overflow: hidden;
    background: var(--backdrop);
    font-family: "Poppins", sans-serif;
  }
  .canvas { position: relative; width: 1200px; height: 900px; }
  .card {
    position: absolute; left: 250px; width: 700px; height: 400px;
    border-radius: 26px; overflow: hidden;
    box-shadow: 0 10px 30px rgba(0,0,0,0.12);
  }
  .card--front { top: 40px; background: var(--brand-blue); }
  .card--back { top: 460px; background: var(--ice-white); }

  .front-lockup {
    position: absolute; left: 0; right: 0; top: 150px;
    display: flex; flex-direction: column; align-items: center;
  }
  .brand-name {
    display: flex; align-items: center; gap: 14px;
    font-weight: 700; font-size: 64px; line-height: 1;
    color: var(--frost); letter-spacing: -0.5px;
  }
  .brand-dot { width: 22px; height: 22px; border-radius: 50%; background: var(--frost); }
  .tagline {
    margin-top: 12px; font-weight: 600; font-size: 20px;
    color: var(--frost); letter-spacing: 0.5px;
  }

  .back-lockup { position: absolute; left: 50px; top: 44px; }
  .back-lockup .brand-name { font-size: 50px; color: var(--brand-blue); gap: 12px; }
  .back-lockup .brand-dot { width: 18px; height: 18px; background: var(--brand-blue); }
  .back-lockup .tagline { font-size: 15px; color: var(--brand-blue); margin-top: 6px; }

  .person {
    position: absolute; left: 50px; top: 176px;
    padding-left: 18px; border-left: 8px solid var(--brand-blue);
  }
  .person-name { font-weight: 700; font-size: 28px; color: var(--brand-blue); line-height: 1.15; }
  .person-role { font-weight: 400; font-size: 16px; color: var(--ink); }

  .address {
    position: absolute; left: 58px; top: 262px;
    font-size: 16px; line-height: 1.35; color: var(--ink);
  }
  .contacts {
    position: absolute; left: 58px; top: 318px;
    list-style: none; font-size: 16px; line-height: 1.4; color: var(--ink);
  }
  .contacts li { display: flex; align-items: center; gap: 10px; }
  .contacts svg { width: 14px; height: 14px; fill: var(--brand-blue); flex: none; }

  .polar-illustration {
    position: absolute; left: 420px; top: 165px;
    width: 230px; height: 235px;
    border-radius: 115px 115px 0 0;
    background: linear-gradient(180deg, #7badd7 0%, var(--brand-blue) 45%, var(--deep-blue) 100%);
  }
</style>
</head>
<body>
<main class="canvas">
  <section class="card card--front">
    <div class="front-lockup">
      <div class="brand-name"><span class="brand-dot"></span>Veltrano.co</div>
      <div class="tagline">Polar Expeditions Specialists</div>
    </div>
  </section>

  <section class="card card--back">
    <div class="back-lockup">
      <div class="brand-name"><span class="brand-dot"></span>Veltrano.co</div>
      <div class="tagline">Polar Expeditions Specialists</div>
    </div>

    <div class="person">
      <div class="person-name">Marcus Thale</div>
      <div class="person-role">CEO &amp; Founder</div>
    </div>

    <div class="address">
      42 Harbor Point Lane,<br>Fairhaven, ME 04011 USA
    </div>

    <ul class="contacts">
      <li>
        <svg viewBox="0 0 24 24" aria-hidden="true"><path d="M6.6 10.8a15.1 15.1 0 0 0 6.6 6.6l2.2-2.2a1 1 0 0 1 1-.25 11.4 11.4 0 0 0 3.6.57 1 1 0 0 1 1 1V20a1 1 0 0 1-1 1A17 17 0 0 1 3 4a1 1 0 0 1 1-1h3.5a1 1 0 0 1 1 1c0 1.25.2 2.45.57 3.57a1 1 0 0 1-.25 1z"/></svg>
        +1.555.010.274
      </li>
      <li>
        <svg viewBox="0 0 24 24" aria-hidden="true"><path d="M2 5h20v14H2zm2 2v.5l8 5 8-5V7l-8 5z"/></svg>
        hello@veltrano.co
      </li>
      <li>
        <svg viewBox="0 0 24 24" aria-hidden="true"><circle cx="12" cy="12" r="10"/></svg>
        www.veltrano.co
      </li>
    </ul>

    <div class="polar-illustration" role="img" aria-label="Large blue silhouette illustration of a polar bear standing with two penguins, with small stars above"></div>
  </section>
</main>
</body>
</html>
```